Corvane Capital Business Cards

These are professional business cards that are for my family office.
Put fake emails and phone numbers as of now until I finalize those components. This family office controls my families investments, assets, and future. The cards should be professional.
..
.
.
.
I just uploaded another variation of a logo I would like to see as a business card to I am inbeteen which logo to use

Target Market(s)

business

Industry/Entity Type

business

Contact Information for Business Card

Professional, wealth related, finance related.

Requirements
Must have
• Logo

```html
<!DOCTYPE html>
<html lang="en">
<head>
<meta charset="utf-8">
<title>Corvane Capital Business Cards</title>
<link rel="stylesheet" href="https://fonts.googleapis.com/css2?family=Playfair+Display:wght@400&family=Tinos:wght@400;700&display=swap">
<style>
  :root {
    --backdrop: #e3e3e1;
    --card: #ffffff;
    --ink: #111111;
    --gold: #c6ae73;
    --shadow: rgba(0, 0, 0, 0.18);
  }
  * { box-sizing: border-box; margin: 0; padding: 0; }
  html, body {
    width: 1200px;
    height: 900px;
    overflow: hidden;
    background: var(--backdrop);
  }
  .canvas {
    position: relative;
    width: 1200px;
    height: 900px;
  }
  .card {
    position: absolute;
    width: 660px;
    height: 377px;
    background: var(--card);
    box-shadow: 0 14px 30px var(--shadow);
    overflow: hidden;
  }
  .card--front { left: 150px; top: 52px; }
  .card--back { left: 390px; top: 470px; }

  .front-wordmark {
    position: absolute;
    left: 0;
    right: 0;
    top: 50%;
    transform: translateY(-50%);
    display: flex;
    align-items: center;
    justify-content: center;
    gap: 18px;
  }
  .front-wordmark__square {
    width: 22px;
    height: 22px;
    background: var(--gold);
  }
  .front-wordmark__name {
    font-family: "Playfair Display", serif;
    font-weight: 400;
    font-size: 46px;
    letter-spacing: 0.06em;
    text-transform: uppercase;
    color: var(--ink);
  }

  .back-wordmark {
    position: absolute;
    left: 44px;
    top: 92px;
    font-family: "Playfair Display", serif;
    font-weight: 400;
    font-size: 24px;
    letter-spacing: 0.06em;
    text-transform: uppercase;
    color: var(--ink);
  }
  .back-accent {
    position: absolute;
    right: 70px;
    top: 90px;
    width: 170px;
    height: 170px;
    background: var(--gold);
  }
  .holder {
    position: absolute;
    left: 44px;
    top: 214px;
    font-family: "Tinos", serif;
    color: var(--ink);
  }
  .holder__name {
    font-weight: 700;
    font-size: 22px;
  }
  .holder__name-last { color: var(--gold); }
  .holder__role {
    font-size: 17px;
    margin-top: 2px;
  }
  .holder__rule {
    width: 22px;
    height: 5px;
    background: var(--gold);
    margin-top: 14px;
  }
  .contact {
    list-style: none;
    margin-top: 18px;
  }
  .contact__item {
    display: flex;
    align-items: center;
    gap: 10px;
    font-size: 18px;
    line-height: 1.45;
  }
  .contact__icon {
    width: 16px;
    height: 16px;
    fill: var(--gold);
    flex: none;
  }
</style>
</head>
<body>
<main class="canvas">
  <section class="card card--front" aria-label="Card front">
    <div class="front-wordmark">
      <span class="front-wordmark__square"></span>
      <span class="front-wordmark__name">Corvane Capital</span>
    </div>
  </section>

  <section class="card card--back" aria-label="Card back">
    <div class="back-wordmark">Corvane Capital</div>
    <div class="back-accent" aria-hidden="true"></div>
    <div class="holder">
      <p class="holder__name">Elias <span class="holder__name-last">Harrow</span></p>
      <p class="holder__role">Founder</p>
      <div class="holder__rule"></div>
      <ul class="contact">
        <li class="contact__item">
          <svg class="contact__icon" viewBox="0 0 16 16" aria-hidden="true">
            <path d="M1 5c0-2 3-3 7-3s7 1 7 3v1h-3V5H4v1H1z"/>
            <path d="M3 7h10l1 7H2z"/>
          </svg>
          <span>555-014-2290</span>
        </li>
        <li class="contact__item">
          <svg class="contact__icon" viewBox="0 0 16 16" aria-hidden="true">
            <path d="M1 3h14v1L8 9 1 4z"/>
            <path d="M1 5.5l7 5 7-5V13H1z"/>
          </svg>
          <span>office@corvanemail.com</span>
        </li>
      </ul>
    </div>
  </section>
</main>
</body>
</html>
```